International Petrochemical business needs a web design for Clearway Desk system

We need a web design for a "Clearway Desk" system for an international petrochemical company. The web site is used internally within the company. It is hosted by an internal department which provides government permit request service for other departments.

We would like to see designs of two pages using color light blue. (home page, internal page as attached).
Home Page:
1. Header has a background image and small animation. Header on home page can be taller than the header of the internal page.
2. Layout as attached.

Internal Page:
1. Header can use the same background image as the home page and can be shorter to utilize the page for content.
2. The blue icon behind every captions represent an icon. When user move mouse over this icon, it displays the caption in Thai language as a tooltip. This icon needs to be redesign.

The final design should communicate the followings:
- Excellent service provided system in terms of time and accurary
- Rapid growth of business via building petrochemical refinery plant
Updates

For Internal Page, the blue circle behind every captions represent an icon. When mouse over this icon, a tool tip showing the caption in Thai language is shown. Please also design this icon..

There are more feedbacks from customer as followed:

1. Banner should consists of 
    1.1 "Approved" stamp on paper
    1.2 An image of Garuda. It is used on every government documents in Thailand
    1.3 Image of petrochemical plant
2. Each menu item (Home, Permit, Search, etc) should have different colors. Drop down menu will use the same color as its parent menu item.
3. Overall tone of the web page should be light blue with background of the body the web page in white
4. "New Request" button should use green color with icon on it
5. Table header of each box in the body of the page should use dark blue background with text in white

Please kindly submit your revisions.
Thank you.

Industry/Entity Type

Business

Requirements
Must have
• 1. Design for 1024x768 screen resolution
2. Use light blue theme
3. Background of header where the company logo is must have white background

```html
<!DOCTYPE html>
<html lang="en">
<head>
<meta charset="utf-8">
<title>Clearway Desk – Home</title>
<link href="https://fonts.googleapis.com/css2?family=Open+Sans:wght@400;600;700&display=swap" rel="stylesheet">
<style>
:root{
  --sky:#1ab4f4;
  --sky-dark:#0fa3e0;
  --link:#1aa9ec;
  --text:#444b50;
  --muted:#5a6064;
  --line:#dcdfe2;
  --cell:#f6f6f6;
  --page:#ffffff;
  --footer:#eeeeee;
  --dot:#b9bcbf;
  --red:#e0141a;
  --amber:#f4c400;
}
*{box-sizing:border-box;margin:0;padding:0}
html,body{width:1103px;height:1200px;overflow:hidden;background:var(--page)}
body{position:relative;font-family:"Open Sans",Arial,sans-serif;color:var(--text);font-size:12px}
.frame-line{position:absolute;width:1px;background:#c9cdd0}
.brand{position:absolute;left:119px;top:34px;display:flex;align-items:center;gap:6px;font-weight:700;font-size:14px;color:var(--sky-dark)}
.brand-mark{width:16px;height:16px;border-radius:50%;background:var(--sky-dark)}
.social{position:absolute;top:31px;left:841px;display:flex;gap:11px}
.social span{width:28px;height:28px;border-radius:3px;background:#3a7fc0}
.social span:nth-child(2){background:#55bfe6}
.social span:nth-child(3){background:#1a6ea8}
.social span:nth-child(4){background:#f27a12}
.banner{position:absolute;left:0;top:108px;width:1103px;height:345px;
  background:linear-gradient(180deg,#1c3d7a 0%,#2c5aa0 45%,#6b85a8 72%,#2b2e2c 86%,#181a18 100%)}
.arrow{position:absolute;top:262px;width:24px;height:38px}
.nav{position:absolute;left:119px;top:85px;width:864px;height:44px;background:linear-gradient(#2ec0f8,#14b0f0);
  border-radius:3px;box-shadow:0 2px 3px rgba(0,0,0,.25);z-index:2}
.nav a{position:absolute;top:15px;color:#fff;font-size:11.5px;font-weight:600;text-decoration:none;letter-spacing:.2px}
.dropdown{position:absolute;left:218px;top:129px;width:163px;height:105px;background:#15b0ee;z-index:2;border-radius:0 0 3px 3px}
.dropdown li{list-style:none;position:absolute;left:17px;color:#fff;font-size:12px;display:flex;align-items:center;gap:11px}
.dropdown li::before{content:"";width:4px;height:4px;background:#fff;box-shadow:2px 3px 0 -1px #fff}
.panel{position:absolute;border:1px solid var(--line);border-radius:3px;background:#fff;overflow:hidden}
.panel-title{height:31px;background:var(--sky);color:#fff;font-weight:600;font-size:13.5px;padding:5px 14px;letter-spacing:.2px}
.grid{display:grid}
.head>div{height:34px;padding:9px 0 0;color:var(--muted);font-size:12px;border-bottom:1px solid var(--line)}
.body>div{background:var(--cell);border-right:1px solid var(--line);line-height:21px;padding-top:12px}
.body>div:last-child{border-right:0}
.grid>div{padding-left:31px}
.grid>div:first-child{padding-left:14px}
.head>div:first-child{padding-left:14px}
.link{color:var(--link)}
.dots{height:32px;border-top:1px solid var(--line);display:flex;gap:5px;padding:12px 0 0 15px}
.dots i{width:8px;height:8px;border-radius:50%;background:var(--dot)}
.flag{display:inline-block;width:14px;height:14px;border-radius:50%;vertical-align:-3px;margin-left:5px}
.expiring-band{position:absolute;left:112px;top:673px;width:878px;height:33px;background:var(--sky);color:#fff;
  font-weight:600;font-size:13.5px;padding:6px 21px;z-index:1}
.btn-new{position:absolute;left:561px;top:861px;width:422px;height:46px;border:1px solid #cfd2d4;border-radius:3px;
  background:linear-gradient(#fbfbfb,#dcdcdc);box-shadow:0 1px 3px rgba(0,0,0,.2);
  font-size:15px;font-weight:600;color:#333;text-align:center;line-height:44px}
.footer{position:absolute;left:0;top:1122px;width:1103px;height:78px;background:var(--footer);border-top:1px solid #d6d6d6;
  text-align:center;padding-top:30px;color:#666;font-size:11.5px}
</style>
</head>
<body>
<div class="frame-line" style="left:110px;top:0;height:108px"></div>
<div class="frame-line" style="left:993px;top:0;height:108px"></div>
<div class="frame-line" style="left:110px;top:453px;height:669px"></div>
<div class="frame-line" style="left:993px;top:453px;height:669px"></div>

<header>
  <div class="brand"><span class="brand-mark"></span>Northline Petrochemical</div>
  <div class="social"><span></span><span></span><span></span><span></span></div>
  <nav class="nav">
    <a style="left:22px">HOME</a>
    <a style="left:115px">PERMITS</a>
    <a style="left:220px">SEARCH</a>
    <a style="left:322px">REPORTS</a>
    <a style="left:428px">ADMIN</a>
    <a style="left:521px">HELP</a>
  </nav>
  <ul class="dropdown">
    <li style="top:17px">Create New Permit</li>
    <li style="top:45px">Transfer Role</li>
    <li style="top:74px">Transfer Res. Person</li>
  </ul>
</header>

<div class="banner" role="img" aria-label="Petrochemical refinery plant lit up at night under a deep blue sky"></div>
<svg class="arrow" style="left:87px" viewBox="0 0 24 38"><path d="M20 3 5 19l15 16" fill="none" stroke="#fff" stroke-width="5"/></svg>
<svg class="arrow" style="left:992px" viewBox="0 0 24 38"><path d="M4 3l15 16L4 35" fill="none" stroke="#fff" stroke-width="5"/></svg>

<section class="panel" style="left:119px;top:470px;width:423px;height:188px">
  <div class="panel-title">New Requests</div>
  <div class="grid head" style="grid-template-columns:115px 161px 1fr"><div>Request No.</div><div>Requested Date</div><div style="padding-left:36px">Branch</div></div>
  <div class="grid body" style="grid-template-columns:115px 161px 1fr;height:93px">
    <div class="link">56-0003<br>56-0004</div><div>20/4/2013<br>20/4/2013</div><div style="padding-left:36px">GC1<br>GC2</div>
  </div>
  <div class="dots"><i></i><i></i><i></i><i></i></div>
</section>

<section class="panel" style="left:561px;top:470px;width:423px;height:188px">
  <div class="panel-title">My Working Requests</div>
  <div class="grid head" style="grid-template-columns:115px 142px 1fr"><div>Request No.</div><div>Requested Date</div><div style="padding-left:24px">Status</div></div>
  <div class="grid body" style="grid-template-columns:115px 142px 1fr;height:93px">
    <div class="link" style="line-height:20px;padding-top:10px">55-0200<br>55-0210<br>55-0300<br>55-0301</div>
    <div style="line-height:20px;padding-top:10px">25/3/2013<br>24/3/2013<br>25/3/2013<br>25/3/2013</div>
    <div style="line-height:20px;padding-top:10px;padding-left:24px">Waiting for Process<br>In Process<br>Incomplete Document<br>Cancel Requested</div>
  </div>
  <div class="dots"><i></i><i></i><i></i><i></i></div>
</section>

<div class="expiring-band">Expiring Permits</div>
<section class="panel" style="left:119px;top:690px;width:865px;height:154px;border-top:0">
  <div style="height:16px"></div>
  <div class="grid head" style="grid-template-columns:115px 142px 165px 94px 164px 1fr">
    <div>Permit No</div><div>Expire Date</div><div>Permit Name</div><div style="padding-left:21px">Branch</div><div>Required Time (Day)</div><div>Due Date</div>
  </div>
  <div class="grid body" style="grid-template-columns:115px 142px 165px 94px 164px 1fr;height:69px">
    <div class="link" style="line-height:22px">AB56001<br>BIO5502</div>
    <div style="line-height:22px">25/3/2013<br>24/3/2013</div>
    <div style="line-height:22px">Permit Name ###10<br>Permit Name ###20</div>
    <div style="line-height:22px;padding-left:21px">GC1<br>GC1</div>
    <div style="line-height:22px">30<span class="flag" style="background:var(--red)"></span><br>60<span class="flag" style="background:var(--amber)"></span></div>
    <div style="line-height:22px">-40<br>-15</div>
  </div>
  <div class="dots" style="height:34px;padding-top:13px"><i></i><i></i><i></i><i></i></div>
</section>

<section class="panel" style="left:120px;top:862px;width:423px;height:243px">
  <div class="panel-title">My In Progress Requests</div>
  <div class="grid head" style="grid-template-columns:115px 143px 1fr"><div>Request No.</div><div>Requested Date</div><div style="padding-left:24px">Status</div></div>
  <div class="grid body" style="grid-template-columns:115px 143px 1fr;height:144px">
    <div class="link" style="line-height:20px">55-0200<br>55-0210<br>55-0300</div>
    <div style="line-height:20px">25/3/2013<br>24/3/2013<br>25/3/2013</div>
    <div style="line-height:20px;padding-left:24px">Waiting for Process<br>In Process<br>Incomplete Document</div>
  </div>
  <div class="dots"><i></i><i></i><i></i><i></i></div>
</section>

<div class="btn-new">New Request</div>

<section class="panel" style="left:561px;top:917px;width:422px;height:189px">
  <div class="panel-title">Recent Completed Requests</div>
  <div class="grid head" style="grid-template-columns:115px 1fr"><div>Request No.</div><div>Complete Date</div></div>
  <div class="grid body" style="grid-template-columns:115px 1fr;height:93px">
    <div class="link" style="line-height:20px">55-0200<br>55-0210<br>55-0300</div>
    <div style="line-height:20px">25/3/2013<br>24/3/2013<br>25/3/2013</div>
  </div>
  <div class="dots"><i></i><i></i><i></i><i></i></div>
</section>

<footer class="footer">Copyright © 2013 Clearway Desk. All Right Reserved</footer>
</body>
</html>
```